Business Card needed ASAPfor Real Estate Investors, company name: Swift Lantern Property Buyers.com

I need this completed ASAP, (today or tomorrow at the latest). Not sure how 10 days ended up as project duration. I have an event coming up and must get them printed ASAP. Thank you for your interest!

We are real estate investors that purchase homes and other types of real estate, and want our brand to identify that. We operate with integrity and we operate fast so that our customers can complete the sales transaction and move on. Want our card to be simple, yet unique and creative. Colors are bright green and orange primarily, (see logo provided)

Industry/Entity Type

Business

Contact Information for Business Card

Logo
Name: Marla Brisbee-Investor
Phone Number: 713-555-0182
Marla@SwiftLanternPropertyBuyers.example
www.swiftlanternpropertybuyers.example

Logo Text

Swift Lantern Property Buyers.com (see logo provided)

Colors
0255a3
9ccb3b
f37122

Requirements
Must have
• see uploaded logo file and card details. Please add nice to haves if it works well with layout, and so that customers know what we are about..
Nice to have
• maybe on front?
• We are a family business built on Integrity, Trust and Professionalism
• Maybe on back?
• Sell us your home and avoid repairs, showings, lost time, and headaches
• Depending on layout and how much room you have.

```html
<!DOCTYPE html>
<html lang="en">
<head>
<meta charset="utf-8">
<title>Swift Lantern Property Buyers — Business Card</title>
<link rel="stylesheet" href="https://fonts.googleapis.com/css2?family=Questrial&display=swap">
<style>
  :root {
    --backdrop: #d9dadb;
    --card-white: #f7f7f5;
    --brand-navy: #0255a3;
    --brand-green: #9ccb3b;
    --brand-orange: #f37122;
    --ink-dark: #4a4a4a;
    --ink-soft: #666666;
    --paper-white: #ffffff;
    --card-shadow: 0 10px 28px rgba(0, 0, 0, 0.22);
  }
  * { box-sizing: border-box; margin: 0; padding: 0; }
  html, body {
    width: 1200px;
    height: 784px;
    overflow: hidden;
    background: var(--backdrop);
    font-family: "Questrial", "Century Gothic", sans-serif;
  }
  .canvas {
    position: relative;
    width: 1200px;
    height: 784px;
    display: flex;
    align-items: center;
    justify-content: center;
    gap: 44px;
  }
  .card {
    position: relative;
    width: 540px;
    height: 309px;
    box-shadow: var(--card-shadow);
  }

  /* Brand lockup */
  .brand {
    display: flex;
    align-items: center;
    gap: 12px;
  }
  .brand-mark {
    width: 26px;
    height: 26px;
    background: var(--brand-green);
    flex: none;
  }
  .brand-name {
    line-height: 1.05;
    font-size: 21px;
    color: var(--brand-navy);
  }
  .brand-sub {
    display: block;
    font-size: 12px;
    letter-spacing: 0.12em;
    text-transform: uppercase;
    padding-left: 2px;
  }

  /* Back: contact side */
  .card-back { background: var(--card-white); }
  .card-back .brand {
    position: absolute;
    top: 34px;
    left: 34px;
  }
  .contact {
    position: absolute;
    left: 250px;
    top: 110px;
    color: var(--ink-soft);
  }
  .contact-name {
    font-size: 25px;
    color: var(--ink-dark);
    font-weight: 400;
    letter-spacing: 0.01em;
  }
  .contact-title {
    font-size: 17px;
    color: var(--brand-orange);
    margin-bottom: 9px;
  }
  .contact-line {
    font-size: 12.5px;
    line-height: 1.62;
  }
  .card-rule {
    position: absolute;
    left: 34px;
    right: 34px;
    bottom: 44px;
    height: 1px;
    background: var(--brand-green);
  }
  .back-tagline {
    position: absolute;
    left: 34px;
    right: 34px;
    bottom: 20px;
    font-size: 11.5px;
    color: var(--brand-navy);
  }

  /* Front: brand side */
  .card-front {
    background: var(--brand-navy);
    display: flex;
    align-items: center;
    justify-content: center;
  }
  .card-front .brand {
    flex-direction: column;
    gap: 14px;
    text-align: center;
    margin-top: -20px;
  }
  .card-front .brand-mark {
    width: 42px;
    height: 42px;
  }
  .card-front .brand-name {
    font-size: 30px;
    color: var(--paper-white);
  }
  .card-front .brand-sub { font-size: 15px; padding-left: 0; }
  .front-tagline {
    position: absolute;
    left: 0;
    right: 0;
    bottom: 30px;
    text-align: center;
    font-size: 12.5px;
    color: var(--brand-orange);
  }
</style>
</head>
<body>
<main class="canvas">
  <section class="card card-back" aria-label="Business card, contact side">
    <div class="brand">
      <span class="brand-mark" aria-hidden="true"></span>
      <p class="brand-name">Swift Lantern<span class="brand-sub">Property Buyers.com</span></p>
    </div>
    <div class="contact">
      <h1 class="contact-name">Marla BRISBEE</h1>
      <p class="contact-title">Investor</p>
      <p class="contact-line">713-555-0182</p>
      <p class="contact-line">Marla@SwiftLanternPropertyBuyers.example</p>
      <p class="contact-line">www.swiftlanternpropertybuyers.example</p>
    </div>
    <div class="card-rule" aria-hidden="true"></div>
    <p class="back-tagline">Sell us your home and avoid repairs, showings, lost time, and headaches</p>
  </section>

  <section class="card card-front" aria-label="Business card, brand side">
    <div class="brand">
      <span class="brand-mark" aria-hidden="true"></span>
      <p class="brand-name">Swift Lantern<span class="brand-sub">Property Buyers.com</span></p>
    </div>
    <p class="front-tagline">A family business built on Integrity, Trust and Professionalism</p>
  </section>
</main>
</body>
</html>
```